Moravel Aesthetic Doctor

I require an elegant, luxurious looking business card for my aesthetic business. I am a doctor and that will set me aside from competitors. I am planning to provide home and spa based treatments to clients with high expectations. I have attached my logo.

```html
<!DOCTYPE html>
<html lang="en">
<head>
<meta charset="utf-8">
<title>Moravel Aesthetic Doctor — Business Card</title>
<link href="https://fonts.googleapis.com/css2?family=Arimo:wght@400;700&display=swap" rel="stylesheet">
<style>
  :root {
    --stage: #101011;
    --card: #1b1b1c;
    --band: #7fcdee;
    --ink-dark: #1b1b1c;
    --silver: #a9aaad;
    --sky: #6cc4ea;
    --muted: #8a8b8e;
    --rule: #4a4b4e;
  }
  * { box-sizing: border-box; margin: 0; padding: 0; }
  html, body {
    width: 1200px; height: 900px; overflow: hidden;
    background: var(--stage);
    font-family: "Arimo", Arial, sans-serif;
  }
  .stage {
    width: 1200px; height: 900px;
    display: flex; flex-direction: column; align-items: center; justify-content: center;
    gap: 44px;
  }
  .card {
    position: relative;
    width: 640px; height: 366px;
    background: var(--card);
    box-shadow: 0 10px 30px rgba(0,0,0,.6);
    overflow: hidden;
  }
  /* front */
  .brand {
    position: absolute; top: 70px; left: 0; right: 0;
    display: flex; align-items: center; justify-content: center; gap: 22px;
  }
  .brand-mark {
    width: 92px; height: 92px; border-radius: 50%;
    border: 3px solid var(--silver);
  }
  .brand-words { display: flex; flex-direction: column; }
  .brand-name {
    font-size: 62px; font-weight: 400; letter-spacing: 3px;
    color: var(--silver); line-height: 1;
  }
  .brand-tag {
    font-size: 21px; font-weight: 400; letter-spacing: 3px;
    color: var(--sky); margin-top: 6px;
  }
  .band {
    position: absolute; left: 0; right: 0;
    background: var(--band);
    display: flex; align-items: center; justify-content: center;
  }
  .front .band { top: 262px; height: 46px; }
  .band-text {
    color: var(--ink-dark); font-size: 17px; letter-spacing: 1px;
  }
  /* back */
  .holder {
    position: absolute; top: 92px; left: 0; right: 0;
    text-align: center;
  }
  .holder-name {
    font-size: 26px; font-weight: 700; color: var(--silver);
  }
  .holder-name .post {
    font-size: 14px; font-weight: 400; color: var(--sky); margin-left: 4px;
  }
  .holder-cred { font-size: 17px; color: var(--sky); margin-top: 4px; }
  .divider {
    width: 150px; height: 1px; background: var(--rule);
    margin: 14px auto 12px;
  }
  .contact { font-size: 16px; color: var(--muted); line-height: 1.35; }
  .contact b { color: var(--sky); font-weight: 700; }
  .contact .web span { color: var(--sky); }
  .back .band { top: 274px; height: 44px; gap: 6px; }
  .social-dot {
    width: 28px; height: 28px; border-radius: 50%;
    border: 2px solid var(--ink-dark);
  }
</style>
</head>
<body>
<main class="stage">
  <section class="card front" aria-label="Card front">
    <div class="brand">
      <div class="brand-mark" aria-hidden="true"></div>
      <div class="brand-words">
        <span class="brand-name">MORAVEL</span>
        <span class="brand-tag">AESTHETIC DOCTOR</span>
      </div>
    </div>
    <div class="band"><span class="band-text">HOME AND SPA BASED TREATMENTS</span></div>
  </section>

  <section class="card back" aria-label="Card back">
    <div class="holder">
      <p class="holder-name">Dr Elise Varnham<span class="post">MRCPCH MD</span></p>
      <p class="holder-cred">Australasian Diploma of Aesthetic Medicine</p>
      <div class="divider"></div>
      <div class="contact">
        <p><b>P:</b> 0800 555 019</p>
        <p><b>E:</b> elise@moravel.co.nz</p>
        <p class="web">www.<span>moravel</span>.co.nz</p>
      </div>
    </div>
    <div class="band">
      <span class="social-dot" aria-label="Social profile"></span>
      <span class="social-dot" aria-label="Social profile"></span>
    </div>
  </section>
</main>
</body>
</html>
```